I need a label design to go on our jars of honey. Our company is called Marrowdale Honey Co. The type of honey is called Fernlight Glen Honey. The jars are 1kg. Attached is the label size. Left hand side needs to have nutritional info... as attached. Middle section is our company name, honey type, 1kg & Whangamata, NZ. Right hand side needs to have info as per photo (raw honey etc). I would like to upload more pictures... but I’m unsure how to do this? Thanks, Carla

Target Market(s)

Honey consumers... families

Industry/Entity Type

Food Production

Colors

Designer to choose colors to be used in the design.

Requirements
Must have
• Nutritional info as per upload
• Type of honey & company name as per upload
• 1kg
• Address
Nice to have
• Similar fonts to upload.
• Possibly background image... floral or beach... very faint though.

```html
<!DOCTYPE html>
<html lang="en">
<head>
<meta charset="utf-8">
<title>Marrowdale Honey Co. – Fernlight Glen Honey Label</title>
<link rel="stylesheet" href="https://fonts.googleapis.com/css2?family=Amatic+SC:wght@400;700&family=Dancing+Script:wght@700&family=Patrick+Hand&family=Open+Sans:wght@400;600&family=Roboto+Condensed:wght@400;700&display=swap">
<style>
  :root {
    --berry-light: #bd4876;
    --berry-mid: #a8325f;
    --berry-deep: #8c1d47;
    --ink: #ffffff;
    --rule: rgba(255,255,255,0.9);
  }
  * { margin: 0; padding: 0; box-sizing: border-box; }
  html, body { width: 1200px; height: 608px; overflow: hidden; background: var(--berry-deep); }
  .label {
    position: relative;
    width: 1200px; height: 608px;
    color: var(--ink);
    overflow: hidden;
  }
  .label-backdrop {
    position: absolute; inset: 0;
    background: radial-gradient(ellipse at 50% 40%, var(--berry-light) 0%, var(--berry-mid) 45%, var(--berry-deep) 100%);
  }
  .panel { position: absolute; text-align: center; }

  /* Left panel */
  .panel-nutrition { left: 47px; top: 56px; width: 242px; font-family: "Open Sans", Arial, sans-serif; }
  .origin { font-size: 16px; line-height: 20px; font-weight: 600; }
  .nutrition-table {
    margin-top: 12px;
    border: 1.5px solid var(--rule);
    text-align: left;
    font-family: "Roboto Condensed", "Arial Narrow", sans-serif;
    font-size: 13px;
  }
  .nutrition-title { font-family: "Open Sans", Arial, sans-serif; font-size: 15px; padding: 3px 8px; border-bottom: 1.5px solid var(--rule); }
  .nutrition-servings { padding: 4px 8px; font-weight: 700; line-height: 16px; border-bottom: 1px solid var(--rule); }
  .nutrition-table table { width: 100%; border-collapse: collapse; }
  .nutrition-table th { font-size: 11px; font-weight: 700; padding: 6px 8px 5px; border-bottom: 1px solid var(--rule); text-align: left; }
  .nutrition-table td { font-weight: 700; padding: 2px 8px; line-height: 17px; }
  .nutrition-table tbody tr:first-child td { padding-top: 6px; }
  .nutrition-table tbody tr:last-child td { padding-bottom: 6px; }
  .storage { margin-top: 18px; font-size: 15.5px; line-height: 20px; }
  .batch-box {
    margin-top: 24px;
    border: 1.5px solid var(--rule);
    height: 86px;
    padding: 6px 10px;
    text-align: left;
    font-size: 15px; line-height: 20px;
  }

  /* Centre panel */
  .panel-brand { left: 330px; width: 540px; top: 86px; }
  .brand-name { font-family: "Open Sans", Arial, sans-serif; font-weight: 600; font-size: 34px; line-height: 44px; letter-spacing: 1px; }
  .honey-type { margin-top: 98px; font-family: "Dancing Script", cursive; font-weight: 700; font-size: 74px; line-height: 80px; }
  .jar-size { margin-top: 82px; font-family: "Amatic SC", cursive; font-weight: 700; font-size: 40px; line-height: 40px; }
  .jar-origin { font-family: "Amatic SC", cursive; font-weight: 700; font-size: 38px; line-height: 40px; letter-spacing: 2px; }

  /* Right panel */
  .panel-story { left: 880px; width: 300px; top: 78px; font-family: "Patrick Hand", cursive; font-size: 19px; line-height: 25px; }
  .panel-story p + p { margin-top: 25px; }
  .panel-story .dedication { margin-top: 50px; }
  .panel-story .contact { margin-top: 50px; }
</style>
</head>
<body>
<main class="label">
  <div class="label-backdrop" role="img" aria-label="Very faint floral pattern over a deep berry gradient"></div>

  <section class="panel panel-nutrition">
    <p class="origin">100% New Zeland Honey<br>No added ingredients</p>
    <div class="nutrition-table">
      <div class="nutrition-title">NUTRITIONAL INFORMATION</div>
      <div class="nutrition-servings">Servings per package: 100<br>Serving size: 10g</div>
      <table>
        <thead>
          <tr><th>Average Quantity</th><th>per Serving</th><th>per 100g</th></tr>
        </thead>
        <tbody>
          <tr><td>Energy</td><td>134kj</td><td>1340kj</td></tr>
          <tr><td>Protein</td><td>0.04g</td><td>0.4g</td></tr>
          <tr><td>Fat total</td><td>0g</td><td>0g</td></tr>
          <tr><td>&nbsp;- saturated</td><td>0g</td><td>0g</td></tr>
          <tr><td>Carbohydrate</td><td>7.9g</td><td>79g</td></tr>
          <tr><td>&nbsp;- sugars</td><td>7.8g</td><td>78.1g</td></tr>
          <tr><td>Sodium</td><td>1.2mg</td><td>12mg</td></tr>
        </tbody>
      </table>
    </div>
    <p class="storage">Store upright in a cool, dry place.<br>No refrigeration needed.<br>Not recomended for infants<br>below the age of 12 months.</p>
    <div class="batch-box">Best before:<br>RMP:<br>Batch No:</div>
  </section>

  <section class="panel panel-brand">
    <h1 class="brand-name">Marrowdale Honey Co.</h1>
    <h2 class="honey-type">Fernlight Glen<br>Honey</h2>
    <p class="jar-size">1KG</p>
    <p class="jar-origin">WHANGAMATA, NZ</p>
  </section>

  <section class="panel panel-story">
    <p>Sourced from the beautiful<br>Coromandel Pensinula.</p>
    <p>Our honey comes to you raw &amp;<br>unpasterurised, ensured it retains<br>all the natural goodness!</p>
    <p>Arohanui,<br>Rob, Carla &amp; boys</p>
    <p class="dedication">'Marrowdale' - all thanks to God for<br>His incredible creation!</p>
    <p class="contact">www.marrowdalehoney.co.nz<br>42 Kowhai Lane<br>Whangamata<br>New Zeland</p>
  </section>
</main>
</body>
</html>
```